Bramwell Crest Electric van design

Looking to design a wrap for a 2021 varenta cargolux high roof using orange black and dark grey colors like in the logo

```html
<!DOCTYPE html>
<html lang="en">
<head>
<meta charset="utf-8">
<title>Bramwell Crest Electric – Van Wrap</title>
<link rel="stylesheet" href="https://fonts.googleapis.com/css2?family=Montserrat:wght@700;800&family=Raleway:wght@400&family=Roboto+Condensed:wght@400&display=swap">
<style>
  :root {
    --orange: #d2593a;
    --charcoal: #3a3a3b;
    --white: #f2f2f2;
    --ring: #ffffff;
    --page: #e6e6e6;
  }
  * { margin: 0; padding: 0; box-sizing: border-box; }
  html, body { width: 686px; height: 1200px; overflow: hidden; background: var(--page); }
  .wrap-sheet { position: relative; width: 686px; height: 1200px; }
  .side-view { position: absolute; left: 20px; top: 40px; width: 646px; height: 300px; }
  .rear-view { position: absolute; left: 133px; top: 420px; width: 420px; height: 720px; }
  .brand-bold { font-family: "Montserrat", sans-serif; font-weight: 800; fill: var(--white); }
  .brand-light { font-family: "Raleway", sans-serif; font-weight: 400; fill: var(--white); }
  .phone { font-family: "Montserrat", sans-serif; font-weight: 700; fill: var(--orange); }
  .web { font-family: "Roboto Condensed", sans-serif; font-weight: 400; fill: var(--orange); }
  .mark-name { font-family: "Montserrat", sans-serif; font-weight: 800; fill: var(--white); }
</style>
</head>
<body>
<main class="wrap-sheet">

  <!-- Side layout -->
  <svg class="side-view" viewBox="0 0 646 300" aria-label="Side wrap layout">
    <defs>
      <clipPath id="side-body"><path d="M10 20 Q12 6 30 6 L520 6 Q560 8 580 60 L630 150 Q640 170 638 230 L636 270 L10 270 Z"/></clipPath>
    </defs>
    <g clip-path="url(#side-body)">
      <rect class="base" x="0" y="0" width="646" height="300" fill="var(--white)"/>
      <rect class="stripe-top" x="0" y="28" width="646" height="10" fill="var(--orange)"/>
      <rect class="name-band" x="0" y="38" width="646" height="72" fill="var(--charcoal)"/>
      <rect class="stripe-mid" x="0" y="110" width="646" height="9" fill="var(--orange)"/>
      <rect class="lower-band" x="0" y="165" width="646" height="22" fill="var(--charcoal)"/>
      <path class="cab-panel" d="M400 6 L646 6 L646 300 L340 300 Q390 250 420 200 Q440 140 400 6 Z" fill="var(--charcoal)"/>
      <circle class="mark-ring" cx="355" cy="100" r="80" fill="var(--ring)"/>
      <circle class="mark-disc" cx="355" cy="100" r="72" fill="var(--orange)"/>
      <text class="mark-name" x="355" y="96" font-size="17" text-anchor="middle">BRAMWELL</text>
      <text class="mark-name" x="355" y="116" font-size="17" text-anchor="middle">CREST</text>
    </g>
    <path d="M10 20 Q12 6 30 6 L520 6 Q560 8 580 60 L630 150 Q640 170 638 230 L636 270 L10 270 Z" fill="none" stroke="var(--charcoal)" stroke-width="2"/>
    <text class="brand-bold" x="30" y="72" font-size="32">BRAMWELL</text>
    <text class="brand-light" x="31" y="102" font-size="26">Crest Electric</text>
    <text class="phone" x="48" y="155" font-size="28">555.014.2290</text>
    <text class="web" x="455" y="160" font-size="11">www.bramwellcrestelectric.com</text>
  </svg>

  <!-- Rear layout -->
  <svg class="rear-view" viewBox="0 0 420 720" aria-label="Rear doors wrap layout">
    <defs>
      <clipPath id="rear-body"><path d="M40 20 Q45 0 80 0 L340 0 Q375 0 380 20 L410 600 L410 690 L10 690 L10 600 Z"/></clipPath>
    </defs>
    <g clip-path="url(#rear-body)">
      <rect x="0" y="0" width="420" height="720" fill="var(--white)"/>
      <rect class="stripe-top" x="0" y="60" width="420" height="22" fill="var(--orange)"/>
      <rect class="name-panel" x="0" y="82" width="420" height="380" fill="var(--charcoal)"/>
      <rect class="stripe-mid" x="0" y="462" width="420" height="22" fill="var(--orange)"/>
      <rect class="bumper" x="0" y="650" width="420" height="40" fill="var(--charcoal)"/>
    </g>
    <line x1="210" y1="0" x2="210" y2="650" stroke="var(--charcoal)" stroke-width="1.5" opacity=".6"/>
    <circle class="mark-ring" cx="210" cy="110" r="64" fill="var(--ring)"/>
    <circle class="mark-disc" cx="210" cy="110" r="58" fill="var(--orange)"/>
    <text class="mark-name" x="210" y="106" font-size="14" text-anchor="middle">BRAMWELL</text>
    <text class="mark-name" x="210" y="124" font-size="14" text-anchor="middle">CREST</text>
    <text class="brand-bold" x="210" y="322" font-size="36" text-anchor="middle">BRAMWELL</text>
    <text class="brand-light" x="210" y="360" font-size="32" text-anchor="middle">Crest Electric</text>
    <rect role="img" aria-label="Electric plug with cord illustration" x="30" y="420" width="90" height="90" rx="20" fill="var(--orange)"/>
    <rect role="img" aria-label="Lightning bolt illustration" x="275" y="500" width="70" height="110" rx="10" fill="var(--orange)"/>
    <text class="phone" x="36" y="565" font-size="28">555.014.2290</text>
    <rect class="web-pill" x="218" y="615" width="176" height="24" rx="5" fill="var(--charcoal)"/>
    <text class="web" x="306" y="632" font-size="11" text-anchor="middle">www.bramwellcrestelectric.com</text>
  </svg>

</main>
</body>
</html>
```